Medical centre needs a business card

We are a medcial centre in Australia, needing a new business card. Our demographic is low working class families. We are going to be renovating our premises to modernise the look and also had a new logo done a few months ago representing quality and community, and now need to update our cards. It needs to be doubled sided, with logo and contact details on the front, and appointment details on the back. . Needs to be modern and simple, easy to read. <br/><br/>Name: Kindle Grove Medical Centre <br/>Address: 512 Parmley Rd (Cnr Parmley Rd & Osgood Creek Rd),<br/>Tindarra Court Shopping Centre, Paralowie, SA 5108<br/>Ph: 08 8461 3072<br/>Tag line: Where your wellbeing comes first<br/>Website: www.kindlegrovemedicalcentre-example.com.au<br/>Online bookings also available<br/><br/>(On the back, to have 3 lines of appointments that can be written in.<br/>Day, date, time)<br/><br/>Your next appointment is on<br/>Can try “M T W Th F Sa Su _________________ at ____________ am/pm” or other combinations <br/>Please advise as soon as possible if unable to attend<br/>Cancellation fees apply if less than 2 hrs notice<br/>Online appointments available (please highlight this option by either by position, colour or font)

Target Market(s)

Lower social economic working class, young families to seniors

Industry/Entity Type

Medical Centre

Contact Information for Business Card

Kindle Grove Medical Centre
512 Parmley Rd (Cnr Parmley Rd & Osgood Creek Drive)
Tindarra Court Shopping Centre
Merrowin SA 5199
Ph: 08 8461 3072
www.kindlegrovemedicalcentre-example.com.au
Tagline line: where your wellbeing comes first
Back side is for appointments
Your next appointment is with Dr ______________
Day/date/time (Please give 3 lines of appointments)
Please advise as soon as possible if unable to attend
Cancellation fees apply if less than 2 hours notice
Online appointments available
Book online easily and conveniently (please highlight online appointments)

Font styles to use
Serif
Sans Serif

Colors

Designer to choose colors to be used in the design.

Requirements
Must have
• Modern and simple
• Easy to ready
• Induces a wellbeing feeling
• Incorporate our logo colours and feel from logo
• Induces feeling of stability and security
Nice to have
• Attract attention
• Pleasant to look at
• Feeling of innovation
Should not have
• Loud clashing colours
• Overly luxurious feeling
• Overly artistic

```html
<!DOCTYPE html>
<html lang="en">
<head>
<meta charset="utf-8">
<title>Kindle Grove Medical Centre – Business Card</title>
<link rel="stylesheet" href="https://fonts.googleapis.com/css2?family=Roboto:wght@400;500;700&display=swap">
<style>
  :root {
    --backdrop: #222222;
    --card-dark: #262626;
    --card-light: #ffffff;
    --brand-blue: #1877c9;
    --brand-sky: #29a3e0;
    --brand-green: #9ccc3c;
    --ink-grey: #777777;
    --rule-grey: #9a9a9a;
    --text-light: #ffffff;
  }
  * { box-sizing: border-box; margin: 0; padding: 0; }
  html, body {
    width: 1200px; height: 900px; overflow: hidden;
    background: var(--backdrop);
    font-family: "Roboto", Arial, sans-serif;
  }
  .stage {
    width: 1200px; height: 900px;
    display: flex; flex-direction: column; align-items: center; justify-content: center;
    gap: 40px;
  }
  .card {
    position: relative;
    width: 620px; height: 344px;
    overflow: hidden;
  }

  /* Appointment side */
  .card--appointment { background: var(--card-light); padding: 38px 48px 0 48px; }
  .brand-name {
    font-weight: 700; letter-spacing: 1.5px; text-transform: uppercase;
    color: var(--brand-blue);
  }
  .card--appointment .brand-name { font-size: 22px; text-align: center; }
  .appointment-intro {
    margin-top: 22px; font-size: 15px; font-weight: 500; letter-spacing: .5px;
    color: var(--brand-blue); display: flex; align-items: flex-end; gap: 6px;
  }
  .appointment-intro .write-line { flex: 1; border-bottom: 1.5px solid var(--brand-blue); height: 1px; margin-bottom: 3px; }
  .write-row {
    display: flex; align-items: flex-end; gap: 8px;
    margin-top: 16px; font-size: 14px; color: var(--ink-grey); letter-spacing: .8px;
  }
  .write-row .write-line { flex: 1; border-bottom: 1px solid var(--rule-grey); margin-bottom: 3px; }
  .write-row--blank { height: 18px; }
  .notice {
    margin-top: 12px; text-align: center; font-size: 13.5px; line-height: 1.4;
    color: var(--ink-grey); letter-spacing: .8px;
  }
  .online-highlight {
    margin-top: 4px; text-align: center; font-size: 15px; font-weight: 500;
    color: var(--brand-green); letter-spacing: .8px;
  }

  /* Contact side */
  .card--contact { background: var(--card-dark); color: var(--text-light); }
  .brand-lockup {
    position: absolute; top: 60px; left: 0; right: 0;
    display: flex; align-items: center; justify-content: center; gap: 12px;
  }
  .brand-dot { width: 22px; height: 22px; border-radius: 50%; background: var(--brand-sky); }
  .card--contact .brand-name { font-size: 24px; color: var(--brand-sky); }
  .tagline {
    position: absolute; top: 104px; left: 0; right: 0; text-align: center;
    font-size: 13px; font-weight: 500; letter-spacing: 1.6px; text-transform: uppercase;
  }
  .divider {
    position: absolute; top: 140px; left: 0; right: 0;
    display: flex; align-items: center; gap: 10px;
  }
  .divider .rule { flex: 1; height: 1.5px; background: var(--brand-blue); }
  .divider .icon { width: 30px; height: 30px; }
  .contact-details {
    position: absolute; top: 186px; left: 0; right: 0; text-align: center;
    font-size: 16px; font-weight: 500; line-height: 1.5; letter-spacing: .8px;
    font-style: normal;
  }
  .accent-line { position: absolute; left: 0; right: 0; bottom: 22px; height: 3px; background: var(--brand-green); }
  .accent-band {
    position: absolute; left: 0; right: 0; bottom: 0; height: 19px;
    background: linear-gradient(90deg, var(--brand-blue), var(--brand-sky));
  }
</style>
</head>
<body>
<main class="stage">

  <section class="card card--appointment" aria-label="Appointment side">
    <h2 class="brand-name">Kindle Grove Medical Centre</h2>
    <p class="appointment-intro">Your next appointment is with Dr <span class="write-line"></span></p>
    <p class="write-row">Day <span class="write-line"></span></p>
    <p class="write-row">date <span class="write-line"></span></p>
    <p class="write-row">time <span class="write-line"></span></p>
    <p class="write-row write-row--blank"><span class="write-line"></span></p>
    <p class="notice">Please advise as soon as possible if unable to attend<br>Cancellation fees apply if less than 2 hours notice</p>
    <p class="online-highlight">Online appointments available.</p>
  </section>

  <section class="card card--contact" aria-label="Contact side">
    <div class="brand-lockup">
      <span class="brand-dot"></span>
      <h1 class="brand-name">Kindle Grove Medical Centre</h1>
    </div>
    <p class="tagline">Where your wellbeing comes first</p>
    <div class="divider">
      <span class="rule"></span>
      <svg class="icon" viewBox="0 0 30 30" aria-label="Phone">
        <circle cx="15" cy="15" r="13" fill="none" stroke="#9ccc3c" stroke-width="1.6"/>
        <path d="M11 8.5c1 0 1.6 2.6 1.3 3.2l-1 1c.6 1.6 1.8 2.9 3.4 3.6l1-1c.6-.4 3.2.3 3.2 1.3l-.4 1.8c-.2.6-.8.9-1.4.8-4-.7-7.2-3.9-7.9-7.9-.1-.6.2-1.2.8-1.4z" fill="#29a3e0"/>
      </svg>
      <svg class="icon" viewBox="0 0 30 30" aria-label="Website">
        <circle cx="15" cy="15" r="13" fill="none" stroke="#9ccc3c" stroke-width="1.6"/>
        <g fill="none" stroke="#29a3e0" stroke-width="1.3">
          <circle cx="15" cy="15" r="7"/>
          <ellipse cx="15" cy="15" rx="3" ry="7"/>
          <line x1="8" y1="15" x2="22" y2="15"/>
          <line x1="9" y1="11.5" x2="21" y2="11.5"/>
          <line x1="9" y1="18.5" x2="21" y2="18.5"/>
        </g>
      </svg>
      <span class="rule"></span>
    </div>
    <address class="contact-details">
      08 8461 3072<br>
      www.kindlegrovemedicalcentre-example.com.au<br>
      512 Parmley Rd (Cnr Parmley Rd &amp; Osgood Creek Drive)<br>
      Tindarra Court Shopping Centre Merrowin SA 5199
    </address>
    <span class="accent-line"></span>
    <span class="accent-band"></span>
  </section>

</main>
</body>
</html>
```